Creation of an elegant and modern turnkey Shopify website

Hello,

We are a new company specializing in the sale of above-ground pools. We want to create a turnkey website, ideally using Shopify. For now, we need a "showcase" site, not an e-commerce platform, with four tabs:

Home Page (an overall presentation of the company)
Our Products (an overview of all the above-ground pools we sell)
Our Projects (a page inspired by Instagram to showcase photos of our future projects)
Contact (a page with all our contact information and a contact form)

We are looking to create a highly visual, elegant, and modern website with vibrant splashes of color. We will provide the text, photos (along with instructions on where to place them on each page), and all other necessary information as attachments.

Thank you in advance for your proposals!

The Brisa Lagoon Team

Target Market(s)

Targeted at Swiss customers (a translator will need to be installed for different languages)

Industry/Entity Type

Sale of customised above-ground pools

Coding

Coded - Design and coding required

Font styles to use
Sans Serif

Colors
0094D4
00A9DD
6FCCEA
C7EBF8
E9F6FB
00AB8E
00BBA5
67D7C9
C6EFE9
E9F9F6

Requirements
Must have
• A stunning, elegant and modern look
Nice to have
• Inspiration from the colors of our logo throughout the site, but in an elegant way
Should not have
• An overly classic look for swimming pool sites

```html
<!DOCTYPE html>
<html lang="en">
<head>
<meta charset="UTF-8">
<title>Brisa Lagoon – Above-Ground Pools</title>
<link href="https://fonts.googleapis.com/css2?family=Inter:wght@300;400;500;600;700&display=swap" rel="stylesheet">
<style>
  :root {
    --page-bg: #E9F9F6;
    --white: #ffffff;
    --ink: #111111;
    --ink-soft: #555555;
    --ink-muted: #8a8a8a;
    --teal: #67D7C9;
    --teal-deep: #00BBA5;
    --blue: #0094D4;
    --sky: #00A9DD;
    --dark-btn: #262626;
    --rule: #cfd8d6;
  }
  * { box-sizing: border-box; margin: 0; padding: 0; }
  html, body { width: 1200px; height: 2917px; overflow: hidden; }
  body {
    position: relative;
    background: var(--page-bg);
    font-family: "Inter", sans-serif;
    color: var(--ink);
  }
  .abs { position: absolute; }

  /* Header */
  .site-header { left: 0; top: 0; width: 1200px; height: 80px; background: var(--white); }
  .brand-name {
    left: 77px; top: 14px; width: 90px;
    font-weight: 300; font-size: 20px; line-height: 24px; letter-spacing: 1px;
    color: var(--sky); text-transform: uppercase;
  }
  .main-nav { top: 31px; font-size: 15px; font-weight: 500; letter-spacing: .3px; white-space: nowrap; }
  .nav-search {
    left: 910px; top: 20px; width: 172px; height: 39px;
    border: 1px solid #e2e2e2; border-radius: 8px;
    font-size: 13px; color: var(--ink-muted);
    display: flex; align-items: center; padding-left: 12px; gap: 12px;
  }

  /* Hero */
  .hero {
    left: 68px; top: 130px; width: 1064px; height: 493px;
    background: linear-gradient(135deg, #2b2f30 0%, #161a1b 45%, #0c1516 70%, #1c2a24 100%);
  }
  .hero-title {
    left: 200px; top: 200px; width: 800px; text-align: center;
    font-size: 54px; line-height: 67px; font-weight: 400; color: var(--white);
  }
  .hero-title strong { font-weight: 700; }
  .btn {
    display: flex; align-items: center; justify-content: center; gap: 14px;
    font-weight: 500; letter-spacing: .3px; white-space: nowrap;
  }
  .btn-hero {
    left: 506px; top: 435px; width: 188px; height: 65px;
    background: var(--white); color: var(--sky); font-size: 17px; font-weight: 600; border-radius: 4px;
  }

  /* Promo row */
  .promo-panel { left: 67px; top: 640px; width: 373px; height: 535px; background: var(--teal); }
  .promo-text {
    left: 73px; top: 803px; width: 361px; text-align: center;
    font-size: 33px; line-height: 38.5px; color: var(--white);
  }
  .btn-explore {
    left: 178px; top: 990px; width: 151px; height: 53px;
    background: var(--white); color: var(--sky); font-size: 15px; font-weight: 600; border-radius: 3px;
  }
  .promo-photo {
    left: 466px; top: 640px; width: 667px; height: 535px;
    background: linear-gradient(160deg, #7ab4dc 0%, #a9cfe6 35%, #d9ebe8 55%, #38c1c3 80%, #e7ece6 100%);
  }

  /* Year-end band */
  .yearend-title { left: 96px; top: 1245px; font-size: 43px; line-height: 63px; font-weight: 500; }
  .yearend-copy { left: 535px; top: 1242px; width: 560px; font-size: 17px; line-height: 25px; color: var(--ink-soft); }
  .btn-dark {
    left: 535px; top: 1313px; width: 185px; height: 53px;
    background: var(--dark-btn); color: var(--white); font-size: 14px; font-weight: 700; border-radius: 4px;
  }

  /* Why choose */
  .section-title {
    left: 300px; top: 1444px; width: 600px; text-align: center;
    font-size: 38px; line-height: 57px; font-weight: 700;
  }
  .feature-card { overflow: hidden; }
  .feature-card .label {
    position: absolute; left: 0; right: 0; text-align: center;
    color: var(--white); font-weight: 700; font-size: 36px; line-height: 44px;
  }
  .card-quality {
    left: 93px; top: 1575px; width: 317px; height: 479px; border-radius: 24px 0 0 24px;
    background: linear-gradient(180deg, #7dcfdc 0%, #9ad7df 40%, #d9a488 65%, #3fb1c2 100%);
  }
  .card-elegant {
    left: 442px; top: 1575px; width: 317px; height: 223px;
    background: linear-gradient(135deg, #2f4a2c 0%, #4a6840 35%, #1d8fab 70%, #8b7357 100%);
  }
  .card-custom {
    left: 442px; top: 1830px; width: 317px; height: 224px;
    background: linear-gradient(180deg, #a9dde3 0%, #8fd2da 60%, #bfe4e6 100%);
  }
  .card-innovation {
    left: 790px; top: 1575px; width: 317px; height: 479px; border-radius: 0 24px 24px 0;
    background: linear-gradient(180deg, #3e6b86 0%, #5f8a97 35%, #7a9b96 60%, #3b5b52 100%);
  }
  .innovation-copy {
    position: absolute; left: 4px; right: 4px; top: 210px; text-align: center;
    color: var(--white); font-size: 20px; line-height: 24.5px;
  }
  .btn-light {
    background: var(--white); color: var(--ink); font-size: 15px;
  }

  /* Contact */
  .contact-photo {
    left: 84px; top: 2137px; width: 517px; height: 344px;
    background: linear-gradient(135deg, #c6ebec 0%, #a7dde1 50%, #bfe6e6 100%);
  }
  .contact-panel { left: 601px; top: 2137px; width: 515px; height: 344px; background: var(--teal); }
  .contact-title { left: 654px; top: 2190px; font-size: 40px; font-weight: 600; color: var(--white); }
  .contact-copy { left: 654px; top: 2271px; width: 420px; font-size: 20px; line-height: 26.5px; color: var(--white); }

  /* Footer */
  .footer-brand {
    left: 110px; top: 2577px; width: 90px;
    font-weight: 300; font-size: 20px; line-height: 24px; letter-spacing: 1px;
    color: var(--sky); text-transform: uppercase;
  }
  .footer-tagline { left: 100px; top: 2659px; font-size: 15px; font-weight: 500; }
  .social-dot { top: 2745px; width: 35px; height: 35px; border-radius: 50%; background: var(--ink); }
  .footer-col { top: 2578px; }
  .footer-col h4 { font-size: 15px; font-weight: 600; margin-bottom: 28px; }
  .footer-col li { list-style: none; font-size: 15px; color: var(--ink-muted); height: 40px; }
  .footer-rule { left: 100px; top: 2846px; width: 999px; height: 1px; background: var(--rule); }
  .copyright { left: 0; top: 2866px; width: 1200px; text-align: center; font-size: 13px; color: #b9c2c0; }
</style>
</head>
<body>

<header class="abs site-header">
  <div class="abs brand-name">Brisa Lagoon</div>
  <nav>
    <span class="abs main-nav" style="left:386px;">HOME</span>
    <span class="abs main-nav" style="left:470px;">OUR PRODUCTS
      <svg width="12" height="8" viewBox="0 0 12 8" style="margin-left:4px"><path d="M1 1.5l5 5 5-5" fill="none" stroke="#111" stroke-width="1.4"/></svg>
    </span>
    <span class="abs main-nav" style="left:645px;">OUR PROJECTS</span>
    <span class="abs main-nav" style="left:790px;">CONTACT</span>
  </nav>
  <div class="abs nav-search">
    <svg width="20" height="20" viewBox="0 0 20 20"><circle cx="9" cy="9" r="7" fill="none" stroke="#9a9a9a" stroke-width="1.4"/><path d="M14 14l4 4" stroke="#9a9a9a" stroke-width="1.4"/></svg>
    Search..
  </div>
  <svg class="abs" style="left:1110px;top:29px" width="18" height="20" viewBox="0 0 18 20"><circle cx="9" cy="10" r="8" fill="none" stroke="#111" stroke-width="1.5"/><path d="M1 10h16M9 2c-3 3-3 13 0 16M9 2c3 3 3 13 0 16" fill="none" stroke="#111" stroke-width="1.2"/></svg>
</header>

<section>
  <div class="abs hero" role="img" aria-label="Dark wooden pool deck with sun loungers beside still water"></div>
  <h1 class="abs hero-title">Transform Your Garden with Our <strong>Premium</strong> Above-Ground <strong>Pools!</strong></h1>
  <a class="abs btn btn-hero">DISCOVER
    <svg width="12" height="20" viewBox="0 0 12 20"><path d="M2 2l8 8-8 8" fill="none" stroke="#00A9DD" stroke-width="2.4"/></svg>
  </a>
</section>

<section>
  <div class="abs promo-panel"></div>
  <p class="abs promo-text">Achieve your dreams with our custom, tailor-made above-ground pools.</p>
  <a class="abs btn btn-explore">EXPLORE
    <svg width="16" height="12" viewBox="0 0 16 12"><path d="M0 6h14M9 1l5 5-5 5" fill="none" stroke="#00A9DD" stroke-width="1.5"/></svg>
  </a>
  <div class="abs promo-photo" role="img" aria-label="Striped turquoise and white beach cabin roof against a blue sky and sea"></div>
</section>

<section>
  <h2 class="abs yearend-title">Get the biggest<br>end of the year</h2>
  <p class="abs yearend-copy">Our exclusive, custom-designed models are crafted to combine style, durability, and innovation, offering a unique and refined experience.</p>
  <a class="abs btn btn-dark">OUR PRODUCTS
    <svg width="16" height="12" viewBox="0 0 16 12"><path d="M0 6h14M9 1l5 5-5 5" fill="none" stroke="#fff" stroke-width="1.5"/></svg>
  </a>
</section>

<section>
  <h2 class="abs section-title">Why Choose Our<br>Above-Ground Pools?</h2>
  <div class="abs feature-card card-quality" role="img" aria-label="Swimmer with sun hat resting in clear turquoise pool water">
    <span class="label" style="top:214px;">Superior Quality</span>
  </div>
  <div class="abs feature-card card-elegant" role="img" aria-label="Tropical resort pool surrounded by palms and thatched roofs">
    <span class="label" style="top:89px;">Elegant Design</span>
  </div>
  <div class="abs feature-card card-custom" role="img" aria-label="Swimmer floating on a pink ring in light blue water">
    <span class="label" style="top:66px;">Custom and<br>Tailor-Made</span>
  </div>
  <div class="abs feature-card card-innovation" role="img" aria-label="Striped beach cabin with parasols under a blue sky">
    <span class="label" style="top:90px;">Constant<br>Innovation</span>
    <p class="innovation-copy">We incorporate the latest technologies to provide you with an optimal and safe swimming experience.</p>
    <a class="abs btn btn-light" style="left:65px;top:340px;width:189px;height:53px;">EXPLORE NOW
      <svg width="16" height="12" viewBox="0 0 16 12"><path d="M0 6h14M9 1l5 5-5 5" fill="none" stroke="#111" stroke-width="1.5"/></svg>
    </a>
  </div>
</section>

<section>
  <div class="abs contact-photo" role="img" aria-label="Aerial view of a swimmer on a pink float in a sparkling pool"></div>
  <div class="abs contact-panel"></div>
  <h2 class="abs contact-title">Contact Us Today</h2>
  <p class="abs contact-copy">Contact us today to discover our range of customizable above-ground pools and get a tailored quote.</p>
  <a class="abs btn btn-light" style="left:653px;top:2378px;width:175px;height:52px;">CONTACT US
    <svg width="16" height="12" viewBox="0 0 16 12"><path d="M0 6h14M9 1l5 5-5 5" fill="none" stroke="#111" stroke-width="1.5"/></svg>
  </a>
</section>

<footer>
  <div class="abs footer-brand">Brisa Lagoon</div>
  <p class="abs footer-tagline">We Bring Your Pool Dreams to Life!</p>
  <span class="abs social-dot" style="left:100px;" aria-label="Social profile"></span>
  <span class="abs social-dot" style="left:149px;" aria-label="Social profile"></span>
  <span class="abs social-dot" style="left:199px;" aria-label="Social profile"></span>

  <div class="abs footer-col" style="left:676px;">
    <h4>About</h4>
    <ul><li>About us</li><li>Features</li><li>Blog</li><li>Projects</li></ul>
  </div>
  <div class="abs footer-col" style="left:815px;">
    <h4>Company</h4>
    <ul><li>How we work</li><li>Press Room</li><li>Jobs</li><li>Community</li></ul>
  </div>
  <div class="abs footer-col" style="left:986px;">
    <h4>Legal</h4>
    <ul><li>Terms of use</li><li>Privacy Policy</li><li>Security Policy</li><li>Cookie Settings</li></ul>
  </div>

  <div class="abs footer-rule"></div>
  <p class="abs copyright">© Copyright 2023 Brisa Lagoon. All rights reserved.</p>
</footer>

</body>
</html>
```